CANNABIS BASED BUSINESS CARD DESIGN AND CREATION

WE ARE A PRIVATELY OWNED INVESTMENT CORPORATION. WE PRIMARILY INVEST IN LEGAL PUBLICALLY TRADED CANNABIS COMPANIES THAT ARE TRADED THROUGH THE OTC OR VOLTRIX. WE OFFER THE PUBLIC AN OPPORTUNITY TO PARTICIPATE DIRECTLY WITH THESE COMPANIES FOR NO FEES, NO COMMISSIONS AND IN DEPTH RESEARCH ON EVERY COMPANY PROFILE. WE ARE ALSO PRO FEDERAL LEGALIZATION AND WILL APPLY FOR CULTIVATION AND DISPENSARY LICENSES WHEN THEY BECOME AVAILABLE.

Target Market(s)

30-60 FEMALE AND MALE INVESTORS

Industry/Entity Type

Business

Contact Information for Business Card

TQM CAPITAL GROUP CORPERIN D SLAUGHTER(469) 426-6302ERIN@EDSCAPITALGROUP.COM

Font styles to use
Decorative

Requirements
Must have
• COMPANY LOGO
• CANNABIS LOGO
Nice to have
• MODERN FONT AND LOGOS

```html
<!DOCTYPE html>
<html lang="en">
<head>
<meta charset="utf-8">
<title>TQM Capital Group Corp – Business Card</title>
<link rel="stylesheet" href="https://fonts.googleapis.com/css2?family=Lato:wght@400&display=swap">
<style>
  :root {
    --backdrop: #2b2b2b;
    --card: #050505;
    --card-edge: #1a1a1a;
    --accent: #f08a1c;
    --text-light: #ffffff;
    --text-soft: #e6e6e6;
  }
  * { margin: 0; padding: 0; box-sizing: border-box; }
  html, body {
    width: 1200px; height: 900px; overflow: hidden;
    background: var(--backdrop);
  }
  .canvas { position: relative; width: 1200px; height: 900px; }

  .card {
    position: absolute;
    width: 564px; height: 320px;
    background: linear-gradient(160deg, #111 0%, var(--card) 60%);
    border-radius: 14px;
    border: 1px solid var(--card-edge);
    box-shadow: 0 10px 30px rgba(0,0,0,.5);
    overflow: hidden;
  }
  .card-front { left: 130px; top: 200px; }
  .card-back  { left: 506px; top: 548px; }

  .brand {
    display: flex; align-items: center; gap: 12px;
    font-family: "Lato", "Helvetica", sans-serif;
    font-weight: 400;
    color: var(--text-light);
    letter-spacing: 1px;
    white-space: nowrap;
  }
  .brand-square {
    background: var(--accent);
    flex: none;
  }

  .card-front .brand {
    position: absolute; left: 0; right: 0; top: 140px;
    justify-content: center; font-size: 30px;
  }
  .card-front .brand-square { width: 22px; height: 22px; }

  .card-back .brand {
    position: absolute; left: 60px; top: 60px; font-size: 22px;
  }
  .card-back .brand-square { width: 16px; height: 16px; }

  .holder {
    position: absolute; left: 60px; top: 150px;
    font-family: "Lato", "Helvetica", sans-serif;
    font-size: 17px; letter-spacing: .5px;
    color: var(--accent);
  }
  .contact-list {
    position: absolute; left: 60px; top: 196px;
    list-style: none;
    font-family: "Lato", "Helvetica", sans-serif;
    font-size: 13px; color: var(--text-soft);
  }
  .contact-list li {
    display: flex; align-items: center; gap: 12px;
    height: 22px;
  }
  .contact-icon { width: 13px; height: 13px; flex: none; }
  .contact-icon path, .contact-icon rect { fill: var(--accent); }
  .contact-icon .stroke { fill: none; stroke: var(--accent); stroke-width: 2; }
  .contact-icon .envelope-fold { fill: none; stroke: var(--card); stroke-width: 1.5; }
</style>
</head>
<body>
<main class="canvas">

  <section class="card card-front" aria-label="Business card front">
    <div class="brand">
      <span class="brand-square"></span>
      <span class="brand-name">TQM CAPITAL GROUP CORP</span>
    </div>
  </section>

  <section class="card card-back" aria-label="Business card back">
    <div class="brand">
      <span class="brand-square"></span>
      <span class="brand-name">TQM CAPITAL GROUP CORP</span>
    </div>

    <p class="holder">MARLA J PENDLEBURY</p>

    <ul class="contact-list">
      <li>
        <svg class="contact-icon" viewBox="0 0 16 16" aria-hidden="true">
          <path d="M1 6c0-3 14-3 14 0v2h-4V6.5H5V8H1z"/>
          <rect x="3" y="8" width="10" height="7" rx="1"/>
        </svg>
        <span>(555) 013-4478</span>
      </li>
      <li>
        <svg class="contact-icon" viewBox="0 0 16 16" aria-hidden="true">
          <rect x="1" y="3" width="14" height="10" rx="1"/>
          <path class="envelope-fold" d="M1 3l7 6 7-6"/>
        </svg>
        <span>marla@tqmcapitalgroup-demo.com</span>
      </li>
      <li>
        <svg class="contact-icon" viewBox="0 0 16 16" aria-hidden="true">
          <path class="stroke" d="M7 9l3-3M6 6L4 8a2.5 2.5 0 003.5 3.5L9.5 9.5M10 10l2-2A2.5 2.5 0 008.5 4.5L6.5 6.5"/>
        </svg>
        <span>www.tqmcapitalgroup-demo.com</span>
      </li>
    </ul>
  </section>

</main>
</body>
</html>
```